Brochure design - tarrow floors

i need a brochure design for my flooring business which is in the same style/theme as the attached file. the images chosen from framequarry should be focused on quality flooring and presented in a corporate and professional way. this design will be intended for printed brochures which i can hand to my clients as part of the sales process... I have a logo which should be included into the design (attached)
Requirements
Must have
- This design should be ready for "Z" folded leaflet format - similar to the file attached
The design should present the images i attached in the brief
the design should follow the theme of the attached complete, sample brochure
the design needs to present the attached company logo in a clear and impressive way.
the design should allow for text boxes near each of the images

```html
<!DOCTYPE html>
<html lang="en">
<head>
<meta charset="utf-8">
<title>Tarrow Floors – Z-fold brochure</title>
<link href="https://fonts.googleapis.com/css2?family=Nunito+Sans:wght@300;400;700&display=swap" rel="stylesheet">
<style>
:root{
  --page:#ffffff;
  --teal:#3aaac4;
  --teal-soft:#5fb6c9;
  --teal-deep:#0e3a45;
  --about-panel:rgba(10,40,48,.88);
  --story-panel:rgba(32,22,16,.9);
  --wood-light:#c9a27a;
  --wood-mid:#b3875d;
  --slate:#4a4f57;
  --slate-dark:#3b3b3d;
  --card:#141414;
  --stripe:rgba(150,150,155,.55);
  --white:#ffffff;
  --text:#e9ecee;
}
*{margin:0;padding:0;box-sizing:border-box}
html,body{width:1200px;height:1200px;overflow:hidden;background:var(--page)}
body{font-family:"Nunito Sans",sans-serif;font-weight:300;color:var(--text);position:relative}
.spread{position:absolute;left:231px;width:746px;height:527px;overflow:hidden}
.spread--outer{top:56px}
.spread--inner{top:621px;background:var(--slate-dark)}
.layer{position:absolute;inset:0;width:100%;height:100%}
.panel{position:absolute;font-size:8.6px;line-height:11.45px}
.panel p{margin-bottom:11.45px}
.panel--about{left:25px;top:74px;width:199px;height:453px;background:var(--about-panel);padding:20px 20px 0 25px}
.panel--about h2{font-weight:300;font-size:14px;color:var(--teal);margin-bottom:14px}
.panel--story{left:272px;top:0;width:201px;height:354px;background:var(--story-panel);padding:96px 20px 0 26px}
.brand-mark{position:absolute;display:flex;flex-direction:column;align-items:center;color:var(--teal);font-weight:400;text-align:center}
.brand-mark__square{background:var(--teal)}
.brand-mark--small{left:322px;top:420px;width:100px}
.brand-mark--small .brand-mark__square{width:14px;height:14px;margin-bottom:5px}
.brand-mark--small .brand-mark__name{font-size:11px;letter-spacing:1.5px}
.brand-mark--large{left:561px;top:404px;width:120px}
.brand-mark--large .brand-mark__square{width:24px;height:24px;margin-bottom:10px}
.brand-mark--large .brand-mark__name{font-size:18px;letter-spacing:2px;line-height:1.1}
.contact{position:absolute;left:300px;top:484px;width:144px;text-align:center;color:var(--teal);font-weight:700;font-size:7.6px;line-height:10px}
.card{position:absolute;background:var(--card)}
.card--top{top:0;height:257px}
.card--bottom{top:271px;height:256px}
.col-1{left:25px;width:199px}
.col-2{left:274px;width:199px}
.col-3{left:523px;width:199px;background:transparent}
.card__photo{position:absolute;left:9px;right:11px;top:25px}
.card--bottom .card__photo{top:13px}
.card__title{position:absolute;left:8px;bottom:5px;color:var(--white);font-weight:400;font-size:13.5px;line-height:17px;text-transform:uppercase}
.card__body{position:absolute;left:9px;right:9px;font-size:6.55px;line-height:8.6px;color:var(--text)}
.service-column{position:absolute;left:523px;top:0;width:199px;height:527px;background:var(--slate)}
</style>
</head>
<body>

<section class="spread spread--outer" aria-label="Outer side of brochure">
  <svg class="layer" viewBox="0 0 746 527" preserveAspectRatio="none">
    <defs>
      <linearGradient id="woodTone" x1="0" y1="0" x2="1" y2="1">
        <stop offset="0" stop-color="#8b6a4d"/>
        <stop offset=".45" stop-color="#c59d76"/>
        <stop offset="1" stop-color="#b68c64"/>
      </linearGradient>
      <linearGradient id="tealTone" x1="0" y1="0" x2="0" y2="1">
        <stop offset="0" stop-color="#62bccf"/>
        <stop offset="1" stop-color="#2f8fa4"/>
      </linearGradient>
    </defs>
    <rect role="img" aria-label="Photo: couple lying smiling on a light oak wooden floor" width="746" height="527" fill="url(#woodTone)"/>
    <polygon role="img" aria-label="Photo: softly lit room with teal curtains" points="0,0 260,0 222,527 0,527" fill="url(#tealTone)"/>
    <polygon points="663,0 746,0 746,527 726,527" fill="rgba(70,70,74,.82)"/>
    <polygon points="263,527 746,253 746,527" fill="rgba(70,70,74,.82)"/>
    <g stroke="#ffffff" stroke-linecap="butt">
      <line x1="354" y1="0" x2="746" y2="194" stroke-width="9"/>
      <line x1="663" y1="0" x2="726" y2="527" stroke-width="8"/>
      <line x1="263" y1="527" x2="746" y2="253" stroke-width="9"/>
    </g>
  </svg>

  <div class="panel panel--about">
    <h2>About us</h2>
    <p>Tarrow Floors is committed to providing clients, both commercial and private, with the premium flooring service they want, when they want it, and at a price which meets their needs. We are passionate about our service delivery and are renowned as leaders in our field, both technically and aesthetically.</p>
    <p>We concentrate almost exclusively on solid wood restoration and installation. Working with everything from oak parquet and pitch pine to maple leisure floors, with a variety of lacquered and oiled finishes. We have an unrivalled reputation for quality. We are known for supplying a service that works because of the extensive knowledge which we have accumulated through our years of experience.</p>
    <p>The retail and hospitality industries face very specific challenges when it comes to flooring: it must be practical and durable, value for money yet aesthetically pleasing, and it must be fashion forward. Furthermore, our service fits these fast pace industries allowing businesses to remain trading for a long as possible whilst restorations are undertaken.</p>
  </div>

  <div class="panel panel--story">
    <p>Residential Floors have their own specific set of challenges in that most of these flooring projects occur within occupied living space. Our team will always strive to undertake work in a clean and dust-free environment, allowing family spaces to remain safe and liveable.</p>
    <p>Above all, we are an ethical company. Our key values are integrity, decency and fairness; values which underline our relationships with customers, suppliers and staff alike. People are at the heart of our business and we believe that our dedication to improving the job satisfaction and performance of our employees is reflected in the level of service to our clients.</p>
  </div>

  <div class="brand-mark brand-mark--small">
    <span class="brand-mark__square"></span>
    <span class="brand-mark__name">TARROW FLOORS</span>
  </div>
  <div class="contact">www.tarrowfloors.co.uk<br>info@tarrowfloors.co.uk</div>

  <div class="brand-mark brand-mark--large">
    <span class="brand-mark__square"></span>
    <span class="brand-mark__name">TARROW<br>FLOORS</span>
  </div>
</section>

<section class="spread spread--inner" aria-label="Inner side of brochure">
  <svg class="layer" viewBox="0 0 746 527" preserveAspectRatio="none">
    <polygon points="486,0 746,0 746,527 512,527" fill="var(--teal)"/>
    <g stroke="var(--stripe)" stroke-width="7">
      <line x1="0" y1="193" x2="400" y2="-20"/>
      <line x1="0" y1="258" x2="440" y2="420"/>
      <line x1="86" y1="0" x2="20" y2="527"/>
      <line x1="330" y1="380" x2="520" y2="527"/>
    </g>
  </svg>
  <div class="service-column"></div>

  <article class="card card--top col-1">
    <div class="card__photo" style="height:162px">
      <svg class="layer" viewBox="0 0 10 10" preserveAspectRatio="none" role="img" aria-label="Photo: floor sanding machine close-up on a wooden floor"><defs><linearGradient id="g1" x1="0" y1="0" x2="1" y2="1"><stop offset="0" stop-color="#7c8a6c"/><stop offset="1" stop-color="#b79a7b"/></linearGradient></defs><rect width="10" height="10" fill="url(#g1)"/></svg>
      <h3 class="card__title">Floor sanding<br>&amp; refinishing</h3>
    </div>
    <p class="card__body" style="top:193px">Sanding and refinishing hardwood floors is what we do best. Whether your floors have just been installed last week or if they're 100 years old, we'll be able to transform them into exactly what you envision. We will be more than happy to take a look at your floors for you and see what we can do for them to make them look amazing again.</p>
  </article>

  <article class="card card--top col-2">
    <div class="card__photo" style="left:8px;right:10px;height:147px">
      <svg class="layer" viewBox="0 0 10 10" preserveAspectRatio="none" role="img" aria-label="Photo: damaged and broken hardwood floorboards"><defs><linearGradient id="g2" x1="0" y1="0" x2="1" y2="1"><stop offset="0" stop-color="#a9602c"/><stop offset=".5" stop-color="#5b4a3a"/><stop offset="1" stop-color="#c76a2a"/></linearGradient></defs><rect width="10" height="10" fill="url(#g2)"/></svg>
      <h3 class="card__title">Floor repairs</h3>
    </div>
    <p class="card__body" style="top:180px">Depending on how well your floors have been taken care of – or if there has been renovations done by previous owners – your hardwood floors may have water damaged areas, gaps from relocated walls, pet and pot plant stains, holes, giant gaps, damaged and splintered boards, previous repairs done by an amateur or any other type of damage. Tarrow Floors can fix these to perfectly blend with your existing floor.</p>
  </article>

  <article class="card card--top col-3">
    <div class="card__photo" style="height:157px">
      <svg class="layer" viewBox="0 0 10 10" preserveAspectRatio="none" role="img" aria-label="Photo: hands sanding a wooden stair tread"><defs><linearGradient id="g3" x1="0" y1="0" x2="1" y2="1"><stop offset="0" stop-color="#e0b27c"/><stop offset="1" stop-color="#b97a42"/></linearGradient></defs><rect width="10" height="10" fill="url(#g3)"/></svg>
      <h3 class="card__title">Stair restoration</h3>
    </div>
    <p class="card__body" style="top:192px">Nothing will standout more in your space than beautifully restored stairs. A staircase is a high-traffic area and can often become worn with a tired appearance. In order to breathe life into your staircase again a tremendous amount of hand work with specialty tools is needed. At Tarrow Floors our team has the skills and expertise to revitalise any staircase and deliver amazing results.</p>
  </article>

  <article class="card card--bottom col-1">
    <div class="card__photo" style="right:7px;height:161px">
      <svg class="layer" viewBox="0 0 10 10" preserveAspectRatio="none" role="img" aria-label="Photo: fan of wood stain sample planks"><defs><linearGradient id="g4" x1="0" y1="0" x2="0" y2="1"><stop offset="0" stop-color="#b9b2a6"/><stop offset=".5" stop-color="#8a5a33"/><stop offset="1" stop-color="#9c4e22"/></linearGradient></defs><rect width="10" height="10" fill="url(#g4)"/></svg>
      <h3 class="card__title">Floor staining</h3>
    </div>
    <p class="card__body" style="top:185px">If you would like to add richness, character and depth to your floor, you may want to consider having them stained. Staining is the process of adding colour to a floor. It's a separate step in the finishing process that is done right after the final sanding and before the finish is applied. This is a highly skilled art form which Tarrow Floors have perfected.</p>
  </article>

  <article class="card card--bottom col-2">
    <div class="card__photo" style="left:8px;right:10px;height:161px">
      <svg class="layer" viewBox="0 0 10 10" preserveAspectRatio="none" role="img" aria-label="Photo: hands laying oak floorboards onto adhesive"><defs><linearGradient id="g5" x1="0" y1="0" x2="1" y2="1"><stop offset="0" stop-color="#c99a62"/><stop offset=".7" stop-color="#d8b485"/><stop offset="1" stop-color="#e6e3de"/></linearGradient></defs><rect width="10" height="10" fill="url(#g5)"/></svg>
      <h3 class="card__title">Floor installation</h3>
    </div>
    <p class="card__body" style="top:185px">Although hardwood floor sanding &amp; restoration is our main specialty, we also install hardwood floors too. You'll be happy to know that we're fully equipped and skilled to do any wood floor installation our clients need. We have years and years of installation experience and have installed hundreds of floors with great results.</p>
  </article>

  <article class="card card--bottom col-3">
    <div class="card__photo" style="height:169px">
      <svg class="layer" viewBox="0 0 10 10" preserveAspectRatio="none" role="img" aria-label="Photo: self-levelling compound being poured onto a subfloor"><defs><linearGradient id="g6" x1="0" y1="0" x2="1" y2="1"><stop offset="0" stop-color="#d6d6d4"/><stop offset="1" stop-color="#9a9a98"/></linearGradient></defs><rect width="10" height="10" fill="url(#g6)"/></svg>
      <h3 class="card__title">Structural<br>floor preparation</h3>
    </div>
    <p class="card__body" style="top:192px">For any flooring project the foundations need to be level and structurally sound. Depending on the condition of your subfloor or subframe, it is often necessary to carry out remedial works. Although this can be a lengthy and challenging process, our team will be on-hand to help.</p>
  </article>
</section>

</body>
</html>
```